Business Card design for a mini spa

business card for a small natural skincare/waxing spa. I need a modern, clean, classy card that draws people in but also need to be able to write future appointments on one side of it.

Target Market(s)

women age 16-70

Industry/Entity Type

Beauty Salon

Contact Information for Business Card

Brisk Skin Care 907-318-2956
2863 W Maltby Kodiak, AK 99608
Facial, Waxing, Spray Tanning,

Colors
33b8a4

Requirements
Must have
• Brisk logo with flower
• my tag line "calm hands, bright days"
• 907-318-2956
• 2863 W Maltby
• a place to write ......Your Next Appointment
• Marta Quennell
Nice to have
• something modern, elegant, clean and simple with my attached logo. I also attached a few pictures of what I like along with a color pallet and a few fonts that I like.
Should not have
• no pictures of people in a spa I do not want your typical spa pictures like stone, people receiving a treatment.

```html
<!DOCTYPE html>
<html lang="en">
<head>
<meta charset="utf-8">
<title>Brisk Skin Care – Business Card</title>
<link href="https://fonts.googleapis.com/css2?family=Amatic+SC:wght@400;700&family=Josefin+Sans:wght@300;400&display=swap" rel="stylesheet">
<style>
  :root {
    --stage: #2e2e2e;
    --teal: #33b8a4;
    --teal-light: #8ad3cb;
    --teal-mid: #5cc2b6;
    --teal-deep: #3c9e93;
    --paper: #ffffff;
    --sand: #d8b887;
    --motif-on-teal: rgba(40, 120, 112, 0.35);
    --motif-on-paper: rgba(92, 194, 182, 0.12);
  }
  * { box-sizing: border-box; margin: 0; padding: 0; }
  html, body { width: 1200px; height: 900px; overflow: hidden; }
  body {
    background: var(--stage);
    display: flex;
    align-items: center;
    justify-content: center;
    gap: 48px;
    font-family: "Amatic SC", cursive;
  }
  .card {
    position: relative;
    width: 320px;
    height: 560px;
    overflow: hidden;
    box-shadow: 0 14px 30px rgba(0,0,0,0.45);
  }
  .wordmark {
    font-family: "Josefin Sans", sans-serif;
    font-weight: 300;
    font-size: 58px;
    letter-spacing: 6px;
    text-transform: uppercase;
    line-height: 1;
    display: flex;
    align-items: center;
    justify-content: center;
    gap: 10px;
  }
  .wordmark-dot {
    width: 12px; height: 12px; border-radius: 50%;
    background: currentColor;
  }
  .subline {
    font-family: "Josefin Sans", sans-serif;
    font-weight: 300;
    font-size: 15px;
    letter-spacing: 2px;
    text-transform: uppercase;
    text-align: center;
    margin-top: 6px;
  }
  .tagline {
    font-weight: 700;
    font-size: 22px;
    letter-spacing: 1px;
    text-align: center;
    margin-top: 8px;
  }
  .motif {
    position: absolute;
    border-radius: 50%;
  }

  /* Front */
  .card-front {
    background: linear-gradient(180deg, var(--teal-light) 0%, var(--teal-mid) 55%, var(--teal) 100%);
    color: var(--paper);
  }
  .card-front .brand { position: absolute; top: 70px; left: 0; right: 0; }
  .card-front .motif {
    left: -20px; top: 300px; width: 360px; height: 320px;
    background: radial-gradient(ellipse at center, var(--motif-on-teal) 0%, rgba(40,120,112,0.15) 55%, rgba(40,120,112,0) 72%);
  }
  .services {
    position: absolute; left: 0; right: 0; bottom: 60px;
    list-style: none; text-align: center;
    font-weight: 700; font-size: 28px; line-height: 1.1; letter-spacing: 1px;
  }

  /* Back */
  .card-back { background: var(--paper); color: var(--teal); }
  .frame {
    position: absolute; inset: 14px;
    border: 1px solid var(--teal-light);
  }
  .card-back .brand { position: absolute; top: 48px; left: 0; right: 0; }
  .card-back .wordmark { font-size: 50px; }
  .card-back .subline { color: var(--sand); }
  .card-back .motif {
    left: 10px; top: 250px; width: 320px; height: 300px;
    background: radial-gradient(ellipse at center, var(--motif-on-paper) 0%, rgba(92,194,182,0.06) 55%, rgba(92,194,182,0) 72%);
  }
  .contact {
    position: absolute; top: 200px; left: 0; right: 0;
    text-align: center;
    font-size: 28px; line-height: 1.15; letter-spacing: 1px;
  }
  .contact-row { display: flex; align-items: center; justify-content: center; gap: 8px; }
  .contact-row svg { width: 18px; height: 18px; fill: var(--teal); }
  .appointment {
    position: absolute; top: 340px; left: 40px; right: 40px;
    text-align: center;
  }
  .appointment-label { color: var(--sand); font-size: 28px; letter-spacing: 1px; }
  .write-line {
    border-bottom: 2px dotted var(--teal);
    height: 52px;
  }
</style>
</head>
<body>

  <section class="card card-front" aria-label="Card front">
    <div class="motif" role="img" aria-label="Large faint flower motif"></div>
    <header class="brand">
      <div class="wordmark">Brisk<span class="wordmark-dot"></span></div>
      <div class="subline">Skin Care</div>
      <div class="tagline">calm hands, bright days</div>
    </header>
    <ul class="services">
      <li>Facial</li>
      <li>Waxing</li>
      <li>Spray Tanning</li>
    </ul>
  </section>

  <section class="card card-back" aria-label="Card back">
    <div class="motif" role="img" aria-label="Faint flower motif"></div>
    <div class="frame"></div>
    <header class="brand">
      <div class="wordmark">Brisk<span class="wordmark-dot"></span></div>
      <div class="subline">Skin Care</div>
      <div class="tagline">calm hands, bright days</div>
    </header>
    <div class="contact">
      <div class="contact-name">Marta Quennell</div>
      <div class="contact-row">
        <svg viewBox="0 0 24 24" aria-hidden="true"><path d="M6.6 10.8a15.1 15.1 0 0 0 6.6 6.6l2.2-2.2a1 1 0 0 1 1-.25 11.4 11.4 0 0 0 3.6.57 1 1 0 0 1 1 1V20a1 1 0 0 1-1 1A17 17 0 0 1 3 4a1 1 0 0 1 1-1h3.5a1 1 0 0 1 1 1c0 1.25.2 2.45.57 3.6a1 1 0 0 1-.25 1z"/></svg>
        <span>907-318-2956</span>
      </div>
      <div class="contact-row">
        <svg viewBox="0 0 24 24" aria-hidden="true"><path d="M21 3 3 10.5l7.5 3 3 7.5z"/></svg>
        <span>2863 W Maltby</span>
      </div>
    </div>
    <div class="appointment">
      <div class="appointment-label">Your Next Appointment</div>
      <div class="write-line"></div>
      <div class="write-line"></div>
    </div>
  </section>

</body>
</html>
```